Computer Training in the Education sector - Letterhead

We need a new letter head to be designed for the company. We provide computer training fro the Education Sector, both primary and private tertiary providers. The colours will need to tie in with the website www.crossingthestream.co.nz.
The company name is Crossing the Stream with the tag line of Computer Training for Educators.
The footer will need to have the following detail...
0508 PCS MENTOR
021 839 415
www.crossingthestream.co.nz / training@crossingthestream.co.nz
Updates

Thanks for the designs so far.

Some have watermarks in the background. Please don't worry about using watermarks as I will not be using a watermark in in a final design.
Regards,
Roger

Thank you for all the designs and the effort. There was some great concepts that came through.

Cheers
Roger

Industry/Entity Type

Computer

```html
<!DOCTYPE html>
<html lang="en">
<head>
<meta charset="utf-8">
<title>Crossing the Stream — Letterhead</title>
<link rel="stylesheet" href="https://fonts.googleapis.com/css2?family=Arimo:wght@400;700&display=swap">
<style>
  :root {
    --backdrop: #e9e6e2;
    --paper: #ffffff;
    --stripe-blue: #3a7cc3;
    --stripe-green: #8cbd44;
    --stripe-orange: #e88a38;
    --ink: #1f1f1f;
    --brand-blue: #2f76c0;
    --rule: #9a9a9a;
  }
  * { box-sizing: border-box; margin: 0; padding: 0; }
  html, body {
    width: 1034px;
    height: 1200px;
    overflow: hidden;
    background: var(--backdrop);
    font-family: "Arimo", Arial, sans-serif;
  }
  .letterhead {
    position: absolute;
    left: 53px;
    top: 0;
    width: 928px;
    height: 1200px;
    background: var(--paper);
  }
  .stripe {
    position: absolute;
    top: 0;
    bottom: 0;
    width: 14px;
  }
  .stripe--blue { left: 0; background: var(--stripe-blue); }
  .stripe--green { left: 18px; background: var(--stripe-green); }
  .stripe--orange { left: 36px; width: 15px; background: var(--stripe-orange); }

  .brand-name {
    position: absolute;
    left: 74px;
    top: 58px;
    width: 140px;
    font-size: 25px;
    line-height: 30px;
    font-weight: 400;
    color: var(--brand-blue);
  }
  .tagline {
    position: absolute;
    left: 229px;
    top: 91px;
    font-size: 17px;
    font-weight: 700;
    letter-spacing: 1.2px;
    color: var(--ink);
  }
  .contact-rule {
    position: absolute;
    left: 636px;
    top: 55px;
    width: 1px;
    height: 95px;
    background: var(--rule);
  }
  .contact {
    position: absolute;
    left: 652px;
    top: 56px;
    list-style: none;
    font-size: 14.5px;
    line-height: 24.5px;
    color: var(--ink);
  }
</style>
</head>
<body>
  <main class="letterhead">
    <div class="stripe stripe--blue"></div>
    <div class="stripe stripe--green"></div>
    <div class="stripe stripe--orange"></div>

    <div class="brand-name">Crossing<br>the Stream</div>
    <p class="tagline">Computer Training for Educators</p>

    <div class="contact-rule"></div>
    <ul class="contact">
      <li>P: 0508 PCS MENTOR</li>
      <li>F: 021 839 415</li>
      <li>E: training@crossingthestream.co.nz</li>
      <li>W: www.crossingthestream.co.nz</li>
    </ul>
  </main>
</body>
</html>
```